Marrowby Water Taxi and Transport Business Card

I need business cards for my new water taxi and freight transport business I have started here in Kodiak Alaska. Kodiak is a remote island in the middle of the gulf of Alaska. There are seven native villages around the island and Kodiak is the #2 fishing port in the United States. We also have the largest Coast Guard Base in the U.S. My company will be providing water taxi and freight transport logistics to the villages and many hunting and fishing lodges as well as remote properties around the island.

I would like a business card that isn't status quo, something that stands out, either in feel or appearance. I do like clean minimal designs but it needs to have the necessary contact info on it.

Target Market(s)

remote lodge / property owners, residents of the many villages around Kodiak and any one wanting to enjoy the great outdoors of Kodiak Alaska

Industry/Entity Type

Business

Contact Information for Business Card

I like clean simple designs that aren't cluttered but still provide the necessary information

Colors
0255a3
3277b5
33a4d5
9bcb3c
add136
fbed22
ffc214
f78f20
f37122

Requirements
Must have
• logo and contact info
• Captain Mason Elwick
• www.marrowbyferryline.com
• mason@marrowbyferryline.com

```html
<!DOCTYPE html>
<html lang="en">
<head>
<meta charset="UTF-8">
<title>Marrowby Water Taxi and Transport – Business Card</title>
<link rel="stylesheet" href="https://fonts.googleapis.com/css2?family=Montserrat:wght@600;700&family=Questrial&display=swap">
<style>
  :root {
    --ocean-blue: #0255a3;
    --mid-blue: #3277b5;
    --sky-blue: #33a4d5;
    --sunset-orange: #f78f20;
    --ink-grey: #6b6f74;
    --rule-grey: #d9dcdf;
    --paper: #ffffff;
    --backdrop: #eceef0;
  }
  * { box-sizing: border-box; margin: 0; padding: 0; }
  html, body {
    width: 1200px;
    height: 950px;
    overflow: hidden;
    background: var(--backdrop);
  }
  .canvas {
    width: 1200px;
    height: 950px;
    display: flex;
    flex-direction: column;
    align-items: center;
    justify-content: center;
    gap: 50px;
  }
  .card {
    width: 700px;
    height: 400px;
    border-radius: 4px;
    box-shadow: 0 6px 18px rgba(0, 0, 0, 0.18);
    position: relative;
    overflow: hidden;
  }

  /* Back of card */
  .card-back {
    background: linear-gradient(135deg, var(--mid-blue) 0%, var(--ocean-blue) 100%);
    display: flex;
    align-items: center;
    justify-content: center;
  }
  .back-mark {
    display: flex;
    align-items: center;
    gap: 14px;
  }
  .back-mark .dot {
    width: 22px;
    height: 22px;
    border-radius: 50%;
    background: var(--sunset-orange);
  }
  .back-mark .wordmark {
    font-family: "Montserrat", sans-serif;
    font-weight: 700;
    font-size: 22px;
    color: var(--paper);
    max-width: 300px;
    line-height: 1.25;
  }

  /* Front of card */
  .card-front {
    background: var(--paper);
    display: flex;
  }
  .brand-panel {
    width: 48%;
    display: flex;
    align-items: center;
    justify-content: center;
    padding: 0 40px;
  }
  .brand-mark {
    display: flex;
    align-items: center;
    gap: 14px;
  }
  .brand-mark .dot {
    flex: none;
    width: 22px;
    height: 22px;
    border-radius: 50%;
    background: var(--sky-blue);
  }
  .brand-mark .wordmark {
    font-family: "Montserrat", sans-serif;
    font-weight: 700;
    font-size: 22px;
    line-height: 1.25;
    color: var(--ocean-blue);
  }
  .divider {
    width: 1px;
    background: var(--rule-grey);
    margin: 60px 0;
  }
  .contact-panel {
    flex: 1;
    padding: 78px 30px 0 36px;
    font-family: "Questrial", sans-serif;
    color: var(--ink-grey);
  }
  .person-name {
    font-family: "Montserrat", sans-serif;
    font-weight: 600;
    font-size: 21px;
    letter-spacing: 0.5px;
    color: var(--ocean-blue);
    text-transform: uppercase;
  }
  .person-title {
    font-size: 16px;
    color: var(--sunset-orange);
    margin-top: 2px;
  }
  .address {
    font-style: normal;
    font-size: 14.5px;
    line-height: 1.5;
    margin-top: 14px;
  }
  .contact-list {
    list-style: none;
    margin-top: 6px;
    font-size: 14.5px;
    line-height: 1.5;
  }
  .contact-list li {
    display: flex;
    align-items: center;
    gap: 10px;
  }
  .contact-list svg {
    width: 14px;
    height: 14px;
    flex: none;
    fill: var(--ocean-blue);
  }
</style>
</head>
<body>
  <main class="canvas">
    <section class="card card-back" aria-label="Card back">
      <div class="back-mark">
        <span class="dot"></span>
        <span class="wordmark">Marrowby Water Taxi and Transport</span>
      </div>
    </section>

    <section class="card card-front" aria-label="Card front">
      <div class="brand-panel">
        <div class="brand-mark">
          <span class="dot"></span>
          <span class="wordmark">Marrowby Water Taxi and Transport</span>
        </div>
      </div>
      <div class="divider"></div>
      <div class="contact-panel">
        <h1 class="person-name">Mason Elwick</h1>
        <p class="person-title">Captain</p>
        <address class="address">
          4120 Harbor View Road<br>
          Anchorage, Alaska 34580
        </address>
        <ul class="contact-list">
          <li>
            <svg viewBox="0 0 24 24" aria-hidden="true"><path d="M6.6 10.8a15.1 15.1 0 0 0 6.6 6.6l2.2-2.2c.3-.3.7-.4 1-.2 1.1.4 2.3.6 3.6.6.6 0 1 .4 1 1V20c0 .6-.4 1-1 1A17 17 0 0 1 3 4c0-.6.4-1 1-1h3.5c.6 0 1 .4 1 1 0 1.3.2 2.5.6 3.6.1.3 0 .7-.2 1l-2.3 2.2z"/></svg>
            555 014 2290
          </li>
          <li>
            <svg viewBox="0 0 24 24" aria-hidden="true"><path d="M2 5h20v14H2V5zm2 2v.5l8 5 8-5V7H4zm16 2.8-8 5-8-5V17h16V9.8z"/></svg>
            mason@marrowbyferryline.com
          </li>
          <li>
            <svg viewBox="0 0 24 24" aria-hidden="true"><path d="M12 2a10 10 0 1 0 0 20 10 10 0 0 0 0-20zm6.9 6h-3a15.7 15.7 0 0 0-1.3-3.8A8 8 0 0 1 18.9 8zM12 4c.8 1.2 1.5 2.5 1.9 4h-3.8c.4-1.5 1.1-2.8 1.9-4zM4.3 14a8 8 0 0 1 0-4h3.4a16.5 16.5 0 0 0 0 4H4.3zm.8 2h3a15.7 15.7 0 0 0 1.3 3.8A8 8 0 0 1 5.1 16zm3-8h-3a8 8 0 0 1 4.3-3.8C8.8 5.4 8.4 6.7 8.1 8zM12 20c-.8-1.2-1.5-2.5-1.9-4h3.8c-.4 1.5-1.1 2.8-1.9 4zm2.3-6H9.7a14.7 14.7 0 0 1 0-4h4.6a14.7 14.7 0 0 1 0 4zm.3 5.8c.6-1.2 1-2.5 1.3-3.8h3a8 8 0 0 1-4.3 3.8zm1.7-5.8a16.5 16.5 0 0 0 0-4h3.4a8 8 0 0 1 0 4h-3.4z"/></svg>
            www.marrowbyferryline.com
          </li>
        </ul>
      </div>
    </section>
  </main>
</body>
</html>
```